Product Designer Business Card

Small product design, engineering and prototyping firm in need of a clean, professional business card design. To support our 3D design and drawing services, we offer 3D printing, molding, and casting of plastics, silicones, resins, etc. Our logo can still be modified/changed if necessary. The red/orange color is preferred, but may be substituted with blue or green, potentially. Either way, the colour of the logo should be match/compliment colors used throughout the design. One thought is to have the logo/contact info on one side, with the other side describing services offered, like with a small icon of 3D printer, molding, casting, and computer with a 3D model on-screen.
Industry/Entity Type
Mechanical Engineering
Contact Information for Business Card
Company: Kelvar Design
Phone: 613-582-9047
Email: mark@kelvardesign.ca

```html
<!DOCTYPE html>
<html lang="en">
<head>
<meta charset="utf-8">
<title>Kelvar Design — Business Card</title>
<link rel="stylesheet" href="https://fonts.googleapis.com/css2?family=Montserrat:wght@400;500;600&display=swap">
<style>
  :root {
    --bg: #161616;
    --card: #232323;
    --card-edge: #2b2b2b;
    --red: #e0261a;
    --white: #f2f2f2;
    --grey: #c9c9c9;
    --emboss: #3a3a3a;
    --icon-tone: #5a5a5a;
  }
  * { box-sizing: border-box; margin: 0; padding: 0; }
  html, body { width: 1200px; height: 900px; overflow: hidden; }
  body {
    background: var(--bg);
    font-family: "Montserrat", sans-serif;
    position: relative;
  }
  .card {
    position: absolute;
    left: 250px;
    width: 700px;
    height: 400px;
    background: linear-gradient(135deg, var(--card) 0%, var(--card-edge) 100%);
    box-shadow: 0 14px 30px rgba(0,0,0,.55);
  }
  .card--back { top: 35px; }
  .card--front { top: 465px; }

  /* back side */
  .back-wordmark {
    position: absolute;
    left: 150px;
    top: 105px;
    width: 380px;
    font-size: 50px;
    font-weight: 600;
    line-height: 1.2;
    color: var(--emboss);
  }
  .back-wordmark span { display: block; }
  .back-wordmark .word-top { padding-left: 60px; letter-spacing: 8px; }
  .back-wordmark .word-bottom { letter-spacing: 22px; }
  .services {
    position: absolute;
    right: 50px;
    top: 40px;
    display: flex;
    flex-direction: column;
    gap: 26px;
    align-items: center;
  }
  .service { display: flex; flex-direction: column; align-items: center; gap: 8px; }
  .service-icon {
    width: 62px;
    height: 62px;
    border-radius: 6px;
    background: linear-gradient(160deg, var(--icon-tone), #3c3c3c);
  }
  .service-label {
    font-size: 13px;
    font-weight: 500;
    letter-spacing: 1px;
    color: var(--grey);
  }

  /* front side */
  .front-brand {
    position: absolute;
    left: 50px;
    top: 125px;
    display: flex;
    align-items: flex-start;
    gap: 14px;
  }
  .brand-dot {
    width: 26px;
    height: 26px;
    margin-top: 14px;
    border-radius: 50%;
    background: var(--red);
  }
  .brand-name {
    font-size: 40px;
    font-weight: 600;
    line-height: 1.25;
    color: var(--white);
  }
  .brand-name span { display: block; }
  .brand-name .word-top { letter-spacing: 6px; }
  .brand-name .word-bottom { letter-spacing: 14px; }
  .divider {
    position: absolute;
    left: 380px;
    top: 110px;
    width: 2px;
    height: 180px;
    background: var(--red);
  }
  .contact {
    position: absolute;
    left: 420px;
    top: 130px;
  }
  .contact-name {
    font-size: 26px;
    font-weight: 600;
    letter-spacing: 1px;
    color: var(--red);
  }
  .contact-title {
    font-size: 16px;
    color: var(--white);
    margin-top: 2px;
    letter-spacing: 1px;
  }
  .contact-lines { margin-top: 26px; display: flex; flex-direction: column; gap: 8px; }
  .contact-line {
    display: flex;
    align-items: center;
    gap: 10px;
    font-size: 17px;
    color: var(--white);
    letter-spacing: .5px;
  }
  .contact-line svg { width: 14px; height: 14px; flex: none; }
</style>
</head>
<body>
  <section class="card card--back">
    <div class="back-wordmark">
      <span class="word-top">Kelvar</span>
      <span class="word-bottom">Design</span>
    </div>
    <div class="services">
      <div class="service">
        <div class="service-icon" role="img" aria-label="Line icon of a molding machine"></div>
        <span class="service-label">Molding</span>
      </div>
      <div class="service">
        <div class="service-icon" role="img" aria-label="Line icon of a 3D printer"></div>
        <span class="service-label">3D printer</span>
      </div>
      <div class="service">
        <div class="service-icon" role="img" aria-label="Line icon representing casting"></div>
        <span class="service-label">Casting</span>
      </div>
    </div>
  </section>

  <section class="card card--front">
    <div class="front-brand">
      <span class="brand-dot"></span>
      <span class="brand-name">
        <span class="word-top">Kelvar</span>
        <span class="word-bottom">Design</span>
      </span>
    </div>
    <div class="divider"></div>
    <div class="contact">
      <div class="contact-name">MARK HALDEN</div>
      <div class="contact-title">President</div>
      <div class="contact-lines">
        <div class="contact-line">
          <svg viewBox="0 0 24 24" aria-hidden="true"><path d="M6.6 10.8a15.1 15.1 0 0 0 6.6 6.6l2.2-2.2a1 1 0 0 1 1-.25 11.4 11.4 0 0 0 3.6.6 1 1 0 0 1 1 1V20a1 1 0 0 1-1 1A17 17 0 0 1 3 4a1 1 0 0 1 1-1h3.5a1 1 0 0 1 1 1 11.4 11.4 0 0 0 .6 3.6 1 1 0 0 1-.25 1z" fill="#e0261a"/></svg>
          613-582-9047
        </div>
        <div class="contact-line">
          <svg viewBox="0 0 24 24" aria-hidden="true"><rect x="2.5" y="5" width="19" height="14" rx="1.5" fill="none" stroke="#e0261a" stroke-width="2"/><path d="M3 6l9 7 9-7" fill="none" stroke="#e0261a" stroke-width="2"/></svg>
          mark@kelvardesign.ca
        </div>
      </div>
    </div>
  </section>
</body>
</html>
```